Willow Cradle Pregnancy and Baby Massage

I need a web design for a new business, WILLOW CRADLE PREGNANCY AND BABY MASSAGE that I am in the process of setting up in the suburbs of Perth, Western Australia. The business is owned and operated by myself and my intention is to service Pregnant Mothers and Parents of Young Babies that would benefit from massage. I would like to have a "Home Page" and pages for "About Me", "Pregnancy Massage", "Baby Massage", a Pricing Page for Pregnancy Massage Sessions, a Pricing Page for Baby Massage Sessions, and a "Contact Me" page to allow clients to either contact me with queries or book available pregnancy massage sessions on a particular day of the week. I would also like a "News" page that would include articles I have written, news about new courses and a link to my Facebook page (yet to be set up). I would like to keep the colour schemes similar to my logo design colours. I need the design to be easy to follow and to appeal to a younger audience (20's to mid 30's).
The target audience is pregnant mothers-to-be wishing to receive massage treatments, and new parents and grandparents of small babies that would like to learn how to massage their babies.
The look and feel should be modern, professional, elegant and feminine.
I need the design to be in a standard format such that I can update the content by myself ( and does not need specialised software) as the company and business progresses.

Target Market(s)

Contact Information for Business Card

Card should have rounded edges. Design should have the same "feel" as the website. Contact Details of my business address, mobile phone, email and website should be included.

Font styles to use
Script

Requirements
Must have
• Same colours as logo design. In cmyk system, the colours are: 20,60,0,0 which best result is pantone 681 and 40,40,0,0 which best result is pantone 2645. Card should include the logo design.

```html
<!DOCTYPE html>
<html lang="en">
<head>
<meta charset="utf-8">
<title>Willow Cradle Pregnancy and Baby Massage</title>
<link href="https://fonts.googleapis.com/css2?family=Cabin:wght@400;500&family=Lato:ital,wght@0,400;0,700;1,400&display=swap" rel="stylesheet">
<style>
:root{
  --lavender:#8f85ba;
  --lavender-dark:#7f76ab;
  --orchid:#b15da6;
  --orchid-soft:#b873ac;
  --card-bg:#ecdce9;
  --blush:#f8f3f4;
  --ink:#4a4a4a;
  --grey:#555;
  --icon-dark:#5f5f66;
  --white:#fff;
}
*{margin:0;padding:0;box-sizing:border-box}
html,body{width:1200px;height:2200px;overflow:hidden;background:var(--white)}
body{position:relative;font-family:"Lato",sans-serif;color:var(--ink)}
.abs{position:absolute}
.heading{font-family:"Cabin",sans-serif;font-weight:400}

/* header */
.brand{left:0;width:1200px;top:18px;text-align:center;font-family:"Lato",sans-serif;color:var(--orchid);font-weight:700;font-size:22px;line-height:1.25}
.brand-dot{display:inline-block;width:16px;height:16px;border-radius:50%;background:var(--orchid);margin-right:8px;vertical-align:middle}
.nav{top:125px;left:0;width:1200px;height:52px;background:var(--lavender)}
.nav a{position:absolute;top:13px;color:var(--white);text-decoration:none;font-size:19px;transform:translateX(-50%);white-space:nowrap}

/* hero */
.hero-photo{top:177px;left:0;width:1200px;height:511px;background:linear-gradient(100deg,#f4efed 0%,#ece4e0 40%,#dcc7bb 70%,#efe9e7 100%)}
.hero-title{top:318px;left:80px;font-size:36px;color:var(--orchid-soft)}
.hero-sub{top:374px;left:297px;font-size:21px;color:var(--orchid-soft)}
.hero-text{top:418px;left:80px;width:470px;font-size:15.5px;line-height:25px;color:var(--ink)}
.btn{display:flex;align-items:center;justify-content:center;font-family:"Cabin",sans-serif;font-size:19px;text-decoration:none}
.btn-hero{top:503px;left:80px;width:185px;height:45px;background:var(--orchid-soft);color:var(--white);border:2px solid #fff}

/* about */
.about-title{top:826px;left:80px;font-size:44px;color:var(--grey)}
.about-text{top:884px;left:80px;width:335px;font-size:15.5px;line-height:25px;color:var(--ink)}
.btn-about{top:1068px;left:78px;width:187px;height:46px;background:var(--lavender);color:var(--white);border:2px solid #b9b2d6}
.card{top:752px;width:312px;height:416px;background:var(--card-bg);border:1.5px solid var(--lavender);border-radius:42px;text-align:center;padding:0 10px}
.card-one{left:444px}
.card-two{left:796px}
.card h3{margin-top:168px;font-family:"Cabin",sans-serif;font-weight:400;font-size:28px;line-height:31px;color:var(--orchid-soft)}
.card p{margin-top:8px;font-size:15px;line-height:25px;color:var(--ink)}
.card a{display:inline-block;margin-top:2px;font-size:16px;color:var(--orchid-soft);text-decoration:underline}

/* benefits */
.divider{top:1222px;left:0;width:1200px;border-top:1.5px dotted #a9a3c8}
.benefits{top:1224px;left:0;width:1200px;height:498px;background:var(--blush)}
.benefits-photo{top:1224px;left:0;width:525px;height:498px;background:linear-gradient(180deg,#efe7e6 0%,#e8cfc4 55%,#f3ece9 100%)}
.benefits-title{top:1294px;left:580px;font-size:43px;line-height:47px;color:var(--lavender)}
.benefits-text{top:1405px;left:580px;width:450px;font-size:15.5px;line-height:25px;color:var(--ink)}
.benefits-text ul{list-style:none}
.benefits-text li::before{content:"•";margin-right:8px}
.btn-benefits{top:1620px;left:578px;width:188px;height:43px;border:2px solid var(--orchid-soft);color:var(--orchid-soft);background:transparent}

/* testimonials */
.testi-title{top:1760px;left:0;width:1200px;text-align:center;font-size:43px;color:var(--orchid-soft)}
.quote-ring{top:1838px;left:124px;width:142px;height:92px}
.avatar{top:1838px;left:174px;width:92px;height:92px;border-radius:50%;background:linear-gradient(135deg,#c9a99a,#7a5a52)}
.quote-text{top:1850px;left:285px;width:730px;font-style:italic;font-size:16px;line-height:27px;color:var(--ink)}
.client{top:1926px;left:885px;width:132px;text-align:right;font-size:18px;color:var(--ink)}
.arrow{top:1872px}

/* footer */
.footer{top:1992px;left:0;width:1200px;height:208px;background:var(--lavender)}
.foot-nav a{position:absolute;top:2022px;color:var(--white);text-decoration:none;font-size:16px;white-space:nowrap}
.foot-rule{top:2075px;left:78px;width:1044px;border-top:1px solid #aaa2cc}
.contact-icon{top:2097px;width:46px;height:46px;border-radius:50%;background:var(--icon-dark);display:flex;align-items:center;justify-content:center}
.contact-text{font-size:15.5px;line-height:23px;color:var(--white)}
.copyright{top:2163px;left:0;width:1200px;text-align:center;font-size:15.5px;color:var(--white)}
.to-top{top:2132px;left:1137px;width:52px;height:52px;border-radius:50%;border:2px solid var(--white);display:flex;align-items:center;justify-content:center}
</style>
</head>
<body>

<header>
  <div class="abs brand"><span class="brand-dot"></span>Willow Cradle<br>Pregnancy and Baby Massage</div>
  <nav class="abs nav">
    <a href="#" style="left:260px">Home</a>
    <a href="#" style="left:385px">About Me</a>
    <a href="#" style="left:510px">benefits</a>
    <a href="#" style="left:640px">Sessions</a>
    <a href="#" style="left:787px">Testimonials</a>
    <a href="#" style="left:932px">Contact</a>
  </nav>
</header>

<section class="hero">
  <div class="abs hero-photo" role="img" aria-label="Photo of a relaxed woman lying on a massage table with a towel under her neck while a therapist's hands rest on her head"></div>
  <h1 class="abs heading hero-title">professional massage service</h1>
  <p class="abs heading hero-sub">to pregnant mothers and babies</p>
  <p class="abs hero-text">Willow Cradle Pregnancy and Baby Massage was launched in 2017, offering massage for pregnant women, and instruction of baby massage to parents, grandparents and carers.</p>
  <a class="abs btn btn-hero" href="#">READ MORE</a>
</section>

<section class="about">
  <h2 class="abs heading about-title">About Me</h2>
  <p class="abs about-text">Maren is a Practitioner of Pregnancy Massage, and a Paediatric Massage Consultant. She completed her training with Prenatal Touch Institute, and the Infant Touch Learning Network. The ITLN is endorsed by the National Midwifery Council.</p>
  <a class="abs btn btn-about" href="#">READ MORE</a>

  <article class="abs card card-one">
    <h3>Pregnancy Massage<br>Session</h3>
    <p>Each session begins with a consultation to assess any high-risk factors, and to review any changes the body has undergone since the last session.</p>
    <a href="#">READ MORE</a>
  </article>
  <article class="abs card card-two">
    <h3>Baby Massage<br>Sessions</h3>
    <p>Introductory Baby Massage Course<br>This class teaches parents and carers the brief basics of Baby massage so they can get started at home.</p>
    <a href="#">READ MORE</a>
  </article>
</section>

<div class="abs divider"></div>
<section>
  <div class="abs benefits"></div>
  <div class="abs benefits-photo" role="img" aria-label="Photo of a pregnant belly with hands forming a heart shape"></div>
  <h2 class="abs heading benefits-title">Benefits of Pregnancy<br>Massage</h2>
  <div class="abs benefits-text">
    <p style="margin-bottom:6px">Pregnancy Massage is a professional relaxation massage that:</p>
    <ul>
      <li>Reduces anxiety caused by hormonal changes</li>
      <li>Improves circulation</li>
      <li>Reduces muscle aches and pain; muscle and joint conditions such as backache, shoulder and neck pain, hip pain, leg cramps, oedema and carpel tunnel</li>
      <li>Relaxes tense muscle, tones loose muscle and increases muscle flexibility.</li>
    </ul>
  </div>
  <a class="abs btn btn-benefits" href="#">READ MORE</a>
</section>

<section>
  <h2 class="abs heading testi-title">Testimonials</h2>
  <svg class="abs arrow" style="left:76px" width="20" height="34" viewBox="0 0 20 34"><path d="M15 3 L4 17 L15 31" fill="none" stroke="#555" stroke-width="2"/></svg>
  <svg class="abs arrow" style="left:1108px" width="20" height="34" viewBox="0 0 20 34"><path d="M5 3 L16 17 L5 31" fill="none" stroke="#555" stroke-width="2"/></svg>
  <svg class="abs quote-ring" viewBox="0 0 142 92">
    <circle cx="46" cy="46" r="45" fill="#fff" stroke="#8f85ba" stroke-width="1.5"/>
    <text x="14" y="62" font-family="Cabin, sans-serif" font-size="46" font-weight="500" fill="#8f85ba">“</text>
  </svg>
  <div class="abs avatar" role="img" aria-label="Client portrait photo"></div>
  <p class="abs quote-text">“ Lorem Ipsum is simply dummy text of the printing and typesetting industry. Lorem Ipsum has been the industry's standard dummy text ever since the 1500s, when an unknown printer took a galley of type and scrambled it to make a type specimen book. ”</p>
  <p class="abs client">— Client Name</p>
</section>

<footer>
  <div class="abs footer"></div>
  <nav class="foot-nav">
    <a href="#" style="left:80px">Home</a>
    <a href="#" style="left:161px">About Me</a>
    <a href="#" style="left:271px">benefits</a>
    <a href="#" style="left:367px">Sessions</a>
    <a href="#" style="left:467px">Testimonials</a>
    <a href="#" style="left:597px">Contact</a>
  </nav>
  <div class="abs foot-rule"></div>

  <div class="abs contact-icon" style="left:77px">
    <svg width="18" height="22" viewBox="0 0 18 22"><path d="M9 1a7.5 7.5 0 0 0-7.5 7.5C1.5 14 9 21 9 21s7.5-7 7.5-12.5A7.5 7.5 0 0 0 9 1z" fill="#fff"/><circle cx="9" cy="8.5" r="2.8" fill="#5f5f66"/></svg>
  </div>
  <p class="abs contact-text" style="top:2097px;left:133px">Maren Ashby Willow Cradle<br>Pregnancy and Infant Massage</p>

  <div class="abs contact-icon" style="left:434px">
    <svg width="20" height="20" viewBox="0 0 24 24"><path d="M6.6 10.8a15 15 0 0 0 6.6 6.6l2.2-2.2a1 1 0 0 1 1-.25 11.4 11.4 0 0 0 3.6.57 1 1 0 0 1 1 1V20a1 1 0 0 1-1 1A17 17 0 0 1 3 4a1 1 0 0 1 1-1h3.5a1 1 0 0 1 1 1c0 1.25.2 2.45.57 3.57a1 1 0 0 1-.25 1z" fill="#fff"/></svg>
  </div>
  <p class="abs contact-text" style="top:2108px;left:493px">041 7360 294</p>

  <div class="abs contact-icon" style="left:795px">
    <svg width="20" height="16" viewBox="0 0 20 16"><rect x="1" y="1" width="18" height="14" rx="1.5" fill="#fff"/><path d="M1.5 2 L10 9 L18.5 2" fill="none" stroke="#5f5f66" stroke-width="1.6"/></svg>
  </div>
  <p class="abs contact-text" style="top:2097px;left:854px;width:270px;word-break:break-all">maren.ashby@willow-cradle.com.au</p>

  <p class="abs copyright">©Willow Cradle - 2017. All Rights Reserved.</p>
  <a class="abs to-top" href="#" aria-label="Back to top">
    <svg width="22" height="14" viewBox="0 0 22 14"><path d="M2 12 L11 3 L20 12" fill="none" stroke="#fff" stroke-width="2.2"/></svg>
  </a>
</footer>

</body>
</html>
```